Plumbing & Heating company

A leaflet containing -

Company name - Larkfield Plumbing Solutions
logo
Mobile number - 07700 914062
Landline - 01632 870215
Email - Info@larkfieldplumbing.example
website - Larkfield-plumbing.example
Social media logos - insta, Facebook

services we offer

- Boiler replacements (free quote)
- General plumbing & heating
- Tap replacements
- 1st & 2nd
- New builds & Extensions
- Cylinder replcemets

```html
<!DOCTYPE html>
<html lang="en">
<head>
<meta charset="utf-8">
<title>Larkfield Plumbing Solutions – Leaflet</title>
<link rel="stylesheet" href="https://fonts.googleapis.com/css2?family=Bricolage+Grotesque:wght@600;700;800&family=Figtree:wght@400;600&family=Sacramento&display=swap">
<style>
  :root {
    --backdrop: #8eaad4;
    --paper: #ffffff;
    --blue: #0795d2;
    --navy: #04559a;
    --orange: #f95d32;
    --ink: #222222;
    --photo-warm: #c9a06a;
    --photo-copper: #8a6a4f;
    --photo-wall: #c7a478;
  }
  * { box-sizing: border-box; margin: 0; padding: 0; }
  html, body { width: 921px; height: 1200px; overflow: hidden; }
  body { background: var(--backdrop); position: relative; font-family: "Figtree", sans-serif; color: var(--ink); }

  .leaflet { position: absolute; left: 97px; top: 86px; width: 727px; height: 1028px; background: var(--paper); overflow: hidden; }

  .brand-script { position: absolute; left: 36px; top: 30px; width: 370px; font-family: "Sacramento", cursive; font-size: 112px; line-height: 1; color: var(--orange); white-space: nowrap; }
  .brand-band { position: absolute; left: 40px; top: 172px; width: 356px; height: 90px; background: var(--blue); transform: rotate(-3deg); transform-origin: left top; overflow: hidden; }
  .brand-band span { position: absolute; left: 16px; top: 2px; font-family: "Bricolage Grotesque", sans-serif; font-weight: 800; font-size: 70px; color: var(--paper); letter-spacing: -1px; line-height: 1.2; white-space: nowrap; }
  .brand-solutions { position: absolute; left: 36px; top: 258px; font-family: "Bricolage Grotesque", sans-serif; font-weight: 800; font-size: 84px; line-height: 1; color: var(--navy); letter-spacing: -2px; white-space: nowrap; }
  .intro { position: absolute; left: 40px; top: 350px; width: 360px; font-size: 15.6px; line-height: 1.3; }

  .logo { position: absolute; left: 454px; top: 58px; width: 241px; display: flex; align-items: center; gap: 10px; }
  .logo-dot { width: 34px; height: 34px; border-radius: 50%; background: var(--orange); flex: none; }
  .logo-name { font-family: "Bricolage Grotesque", sans-serif; font-weight: 800; font-size: 24px; line-height: 1.05; color: var(--navy); }

  .photo { position: absolute; }
  .photo-hero { left: 454px; top: 176px; width: 240px; height: 397px; border-radius: 4px; background: linear-gradient(160deg, #f2d9a0 0%, var(--photo-warm) 45%, #3d5d8f 100%); }
  .photo-pipework { left: 46px; top: 432px; width: 165px; height: 124px; transform: rotate(-3deg); background: linear-gradient(135deg, #6d6a63, var(--photo-copper) 55%, #5b5850); }
  .photo-boiler { left: 206px; top: 440px; width: 165px; height: 124px; transform: rotate(3deg); background: linear-gradient(135deg, var(--photo-wall), #e8e4dc 55%, #b08c63); }

  .services-title { position: absolute; left: 40px; top: 568px; font-family: "Bricolage Grotesque", sans-serif; font-weight: 700; font-size: 24px; color: var(--navy); }
  .services-title em { font-style: normal; color: var(--orange); }

  .service { position: absolute; width: 196px; height: 142px; color: var(--paper); padding: 9px 4px 0 34px; overflow: hidden; }
  .service--blue { background: var(--blue); }
  .service--navy { background: var(--navy); }
  .service--orange { background: var(--orange); }
  .service-icon { position: absolute; left: 10px; top: 13px; width: 16px; height: 16px; }
  .service h3 { font-family: "Bricolage Grotesque", sans-serif; font-weight: 700; font-size: 20px; line-height: 1.05; }
  .service p { margin-top: 6px; font-size: 13px; line-height: 1.26; }
  .service--tight p { margin-top: 3px; font-size: 12.4px; line-height: 1.22; }

  .col-1 { left: 39px; } .col-2 { left: 270px; } .col-3 { left: 497px; }
  .row-1 { top: 608px; } .row-2 { top: 778px; }

  .service--quote { padding: 0; background: var(--navy); }
  .quote-top { position: relative; height: 73px; background: var(--blue); padding: 12px 6px 0 37px; }
  .quote-action { display: block; text-align: center; font-family: "Bricolage Grotesque", sans-serif; font-weight: 700; font-size: 26px; line-height: 69px; }

  .contacts-label { position: absolute; left: 40px; top: 944px; font-family: "Bricolage Grotesque", sans-serif; font-weight: 700; font-size: 21px; color: var(--navy); }
  .social { position: absolute; left: 41px; top: 982px; display: flex; gap: 10px; }
  .social span { width: 18px; height: 18px; border-radius: 50%; background: var(--orange); }
  .social span + span { background: var(--navy); }
  .contact { position: absolute; display: flex; align-items: center; gap: 12px; font-family: "Bricolage Grotesque", sans-serif; font-weight: 600; font-size: 20px; color: var(--ink); white-space: nowrap; }
  .contact svg { width: 18px; height: 18px; flex: none; }
  .contact--mobile { left: 149px; top: 942px; }
  .contact--landline { left: 149px; top: 972px; }
  .contact--email { left: 356px; top: 942px; }
  .contact--web { left: 356px; top: 972px; }
</style>
</head>
<body>
<main class="leaflet">
  <div class="brand-script">Larkfield</div>
  <div class="brand-band"><span>Plumbing</span></div>
  <div class="brand-solutions">Solutions</div>
  <p class="intro">Larkfield Plumbing Solutions are a young and ambitious Plumbing &amp; Heating company with close to a decade of experience.</p>

  <div class="logo"><span class="logo-dot"></span><span class="logo-name">Larkfield Plumbing Solutions</span></div>

  <div class="photo photo-hero" role="img" aria-label="Photo of a plumber in overalls fixing pipework under a bathroom basin"></div>
  <div class="photo photo-pipework" role="img" aria-label="Photo of new copper pipe runs between floor joists"></div>
  <div class="photo photo-boiler" role="img" aria-label="Photo of a newly installed wall-mounted boiler with pipework"></div>

  <h2 class="services-title">Our <em>Services</em></h2>

  <section class="service service--blue col-1 row-1">
    <svg class="service-icon" viewBox="0 0 16 16" fill="#fff"><rect x="2" y="4" width="11" height="4" rx="1"/><rect x="6" y="1" width="5" height="2"/><rect x="2" y="8" width="3" height="4"/><circle cx="3.5" cy="14.5" r="1.3"/></svg>
    <h3>Tap Replacements</h3>
    <p>A cold outside tap is good, but a warm outside tap is even better.</p>
  </section>

  <section class="service service--navy col-2 row-1">
    <svg class="service-icon" viewBox="0 0 16 16" fill="#fff"><rect x="1" y="2" width="14" height="3" rx="1"/><rect x="7" y="5" width="3" height="10" rx="1"/></svg>
    <h3>General Plumbing &amp; Heating</h3>
    <p>Heating is an extremely efficient way of running your home.</p>
  </section>

  <section class="service service--orange service--tight col-3 row-1">
    <svg class="service-icon" viewBox="0 0 16 16" fill="none" stroke="#fff" stroke-width="2"><path d="M3 1v7a5 5 0 0 0 10 0V1"/></svg>
    <h3>New builds &amp; Extensions</h3>
    <p>New build &amp; extensions involves a meticulous process that ensures, functionality, efficiency, &amp; Compliance.</p>
  </section>

  <section class="service service--orange col-1 row-2">
    <svg class="service-icon" viewBox="0 0 16 16" fill="#fff"><rect x="3" y="0" width="10" height="13" rx="2"/><rect x="6" y="13" width="4" height="3"/></svg>
    <h3>Boiler Replacements</h3>
    <p>We offer boiler replacements with 10 year parts and labour warranty.</p>
  </section>

  <section class="service service--blue col-2 row-2">
    <svg class="service-icon" viewBox="0 0 16 16" fill="#fff"><rect x="7" y="0" width="3" height="16"/><rect x="1" y="6" width="14" height="3"/></svg>
    <h3>1st &amp; 2nd</h3>
    <p>At LPS we pride ourselves on completing work to the highest of standards.</p>
  </section>

  <section class="service service--quote col-3 row-2">
    <div class="quote-top">
      <svg class="service-icon" viewBox="0 0 16 16" fill="#fff"><rect x="4" y="2" width="8" height="14" rx="3"/><rect x="6" y="0" width="4" height="2"/></svg>
      <h3>Cylinder Replacements</h3>
    </div>
    <span class="quote-action">Free Quote</span>
  </section>

  <h2 class="contacts-label">Contacts</h2>
  <div class="social"><span></span><span></span></div>

  <div class="contact contact--mobile">
    <svg viewBox="0 0 24 24" fill="var(--navy)"><path d="M6.6 10.8a15 15 0 0 0 6.6 6.6l2.2-2.2a1 1 0 0 1 1-.25 11.4 11.4 0 0 0 3.6.57 1 1 0 0 1 1 1V20a1 1 0 0 1-1 1A17 17 0 0 1 3 4a1 1 0 0 1 1-1h3.5a1 1 0 0 1 1 1c0 1.250.2 2.45.57 3.57a1 1 0 0 1-.25 1z"/></svg>
    07700 914062
  </div>
  <div class="contact contact--landline">
    <svg viewBox="0 0 24 24" fill="var(--orange)"><path d="M6.6 10.8a15 15 0 0 0 6.6 6.6l2.2-2.2a1 1 0 0 1 1-.25 11.4 11.4 0 0 0 3.6.57 1 1 0 0 1 1 1V20a1 1 0 0 1-1 1A17 17 0 0 1 3 4a1 1 0 0 1 1-1h3.5a1 1 0 0 1 1 1c0 1.250.2 2.45.57 3.57a1 1 0 0 1-.25 1z"/></svg>
    01632 870215
  </div>
  <div class="contact contact--email">
    <svg viewBox="0 0 24 24" fill="var(--orange)"><path d="M2 5h20v14H2z"/><path d="M2 5l10 7 10-7" fill="none" stroke="#fff" stroke-width="2"/></svg>
    Info@larkfieldplumbing.example
  </div>
  <div class="contact contact--web">
    <svg viewBox="0 0 24 24" fill="var(--navy)"><path d="M5 2l14 10-6 1.5 3.5 7-3 1.5-3.5-7L5 19z"/></svg>
    Larkfield-plumbing.example
  </div>
</main>
</body>
</html>
```